Product label for herbal salves, lotions, soaps and tinctures

We need a very simple, clean and organic looking label that can be used for an ointment jar, a lotion bottle and a dropper bottle.
We have an existing logo (see attached). We like the colors white, olive green, gold and black. It needs to include product name as dominant and logo. It also needs to include an ingredient list, and usage statement. Include weight of product, distributed by, made in the USA, and QVX statement.
Example of what needs to be present:
Logo
Name: Tranquil Ease Blend
Used for: For Muscle Aches, Arthritis, Tendonitis, Headaches
To Use: For muscle aches, arthritis and tendonitis, massage into affected area. For tension headache apply to neck, temples and forehead.
Store in a cool and dry place, away from direct heat and sunlight.
Weight of product: 1.75
DIST. BY: Copper Brook Herbal
Made in the USA
This product is not intended to diagnose, treat, cure
or prevent any disease. Not regulated
by the QVX. Please consult your health care practitioner
before using product. Discontinue use if any adverse reaction occurs.
Ingredient list:
Wildcrafted Ingredients:
Ashwagandha Root, Peppermint Leaf, Hops Flowers, St. John’s Wort Herb, Arnica Flowers, Green Tea Leaf, Alfalfa Leaf, Dandelion Root, Burdock Root, Chickweed Herb, Chaparral Leaf, Yarrow Flowers, Boneset Herb, Moringa Leaf, Meadowsweet Herb, Nettle Leaf
Organic Ingredients:
Olive Oil, Aloe Leaf, Sweet Birch Bark, Helichrysum Flowers, Holy Basil Leaf, Borage Herb, Ginger Root, Angelica Root, White Willow Bark, Mustard Seed, Beeswax, Vitamin E, Essential Oils
Dimensions of Jar:
Circumference: 7 in.
Height: 1 in.

```html
<!DOCTYPE html>
<html lang="en">
<head>
<meta charset="utf-8">
<title>Copper Brook Herbal – Tranquil Ease Blend Labels</title>
<link rel="stylesheet" href="https://fonts.googleapis.com/css2?family=Playfair+Display:wght@700&family=Marcellus&family=Barlow:wght@400;600&display=swap">
<style>
  :root {
    --paper: #ffffff;
    --label: #f4f4f4;
    --olive: #6a6f35;
    --olive-faint: #c9cbbd;
    --ink: #2b2b2b;
    --ink-soft: #3d3d3d;
    --gold-dark: #8a5a22;
    --gold: #b8944a;
    --gold-light: #e8d48a;
  }
  * { box-sizing: border-box; margin: 0; padding: 0; }
  html, body { width: 1200px; height: 1200px; overflow: hidden; background: var(--paper); }
  .canvas { position: relative; width: 1200px; height: 1200px; background: var(--paper); }

  .brand-mark {
    position: absolute; left: 0; top: 270px; width: 1200px;
    text-align: center;
    font-family: "Playfair Display", serif; font-weight: 700;
    font-size: 70px; line-height: 1; color: var(--olive);
  }

  .label {
    position: absolute; background: var(--label);
    display: flex; flex-direction: column; align-items: center;
    overflow: hidden;
  }
  .gold-band {
    position: absolute; left: 0; width: 100%; height: 9px;
    background: linear-gradient(90deg, var(--gold-dark) 0%, var(--gold) 25%, var(--gold-light) 45%, var(--gold) 65%, var(--gold-dark) 80%, var(--gold-light) 100%);
  }
  .gold-band.top { top: 0; }
  .gold-band.bottom { bottom: 0; }

  .label-brand {
    font-family: "Playfair Display", serif; font-weight: 700;
    color: var(--olive); text-align: center; line-height: 1.05;
  }
  .product-name {
    font-family: "Marcellus", serif; color: var(--ink);
    text-align: center; line-height: 1.2; letter-spacing: 0.5px;
    position: relative; z-index: 1;
  }
  .uses {
    font-family: "Barlow", sans-serif; color: var(--ink-soft);
    border-left: 1.5px solid var(--ink-soft); line-height: 1.35;
    position: relative; z-index: 1;
  }
  .weight {
    font-family: "Barlow", sans-serif; font-weight: 600; color: var(--ink);
    letter-spacing: 0.2px;
  }
  .decor-dot {
    position: absolute; border-radius: 50%; background: var(--olive-faint); opacity: 0.45;
  }

  /* roll-on label */
  .label-rollon { left: 78px; top: 703px; width: 287px; height: 390px; }
  .label-rollon .label-brand { font-size: 27px; margin-top: 78px; width: 200px; }
  .label-rollon .product-name { font-size: 22px; margin-top: 46px; }
  .label-rollon .uses { font-size: 13px; margin-top: 20px; padding-left: 12px; align-self: flex-start; margin-left: 98px; }
  .label-rollon .weight { font-size: 11px; margin-top: 16px; }
  .label-rollon .decor-dot { width: 40px; height: 50px; left: 180px; top: 260px; }

  /* jar label */
  .label-jar { left: 410px; top: 933px; width: 395px; height: 195px; }
  .label-jar .product-name { font-size: 26px; margin-top: 32px; }
  .jar-row { display: flex; align-items: center; margin-top: 18px; gap: 24px; }
  .label-jar .label-brand { font-size: 23px; width: 130px; }
  .label-jar .uses { font-size: 13px; padding-left: 10px; }
  .label-jar .decor-dot { width: 30px; height: 46px; left: 192px; top: 112px; }

  /* spray label */
  .label-spray { left: 856px; top: 497px; width: 264px; height: 565px; }
  .label-spray .label-brand { font-size: 28px; margin-top: 118px; width: 200px; }
  .label-spray .product-name { font-size: 23px; margin-top: 82px; }
  .label-spray .uses { font-size: 14px; margin-top: 50px; padding-left: 12px; align-self: flex-start; margin-left: 72px; }
  .label-spray .weight { font-size: 11px; margin-top: 40px; }
  .label-spray .decor-dot { width: 30px; height: 38px; left: 96px; top: 372px; }
</style>
</head>
<body>
<main class="canvas">
  <div class="brand-mark">Copper Brook Herbal</div>

  <section class="label label-rollon">
    <div class="gold-band top"></div>
    <div class="decor-dot" role="img" aria-label="Faint botanical accent"></div>
    <div class="label-brand">Copper Brook Herbal</div>
    <h2 class="product-name">TRANQUIL EASE<br>BLEND</h2>
    <p class="uses">Muscle Aches<br>Arthritis<br>Tendonitis<br>Headaches</p>
    <p class="weight">WEIGHT: 1.75 OZ</p>
    <div class="gold-band bottom"></div>
  </section>

  <section class="label label-jar">
    <div class="gold-band top"></div>
    <div class="decor-dot" role="img" aria-label="Faint botanical accent"></div>
    <h2 class="product-name">TRANQUIL EASE BLEND</h2>
    <div class="jar-row">
      <div class="label-brand">Copper Brook Herbal</div>
      <p class="uses">Muscle Aches<br>Arthritis<br>Tendonitis<br>Headaches</p>
    </div>
    <div class="gold-band bottom"></div>
  </section>

  <section class="label label-spray">
    <div class="gold-band top"></div>
    <div class="decor-dot" role="img" aria-label="Faint botanical accent"></div>
    <div class="label-brand">Copper Brook Herbal</div>
    <h2 class="product-name">TRANQUIL EASE<br>BLEND</h2>
    <p class="uses">Muscle Aches<br>Arthritis<br>Tendonitis<br>Headaches</p>
    <p class="weight">WEIGHT: 1.75 OZ</p>
    <div class="gold-band bottom"></div>
  </section>
</main>
</body>
</html>
```